Refresh of far from plain IT company website

Our web site is starting to show it's age. You can see the existing site here: www.plumbwick.net. As a growing company we want to come across as a dynamic collection of IT experts.

We want to update the design so are open to any colour palette and look, but want to retain our current table logo. We use the logo on our business cards but with a white background - see the attached file, so you don't need to keep the brown or the green.

The design should consider the range of browsers that will be looking at the site - so please show how it will look on a wide screen laptop and a 768x1024 tablet.

We want to add some pages about our team and their skills, probably with photos of each person on the team.

This is an uncoded project - the PSD files of the design is required, not coding.
Updates

Thanks everyone for the submissions so far.  It's a holiday day in the UK today but we will get some feedback on the designs so far out to you.

Target Market(s)

Architects and other creative types looking for IT support

Industry/Entity Type

Business

Font styles to use
Serif
Sans Serif

Requirements
Must have
• Must look good on a laptop and an iPad.

```html
<!DOCTYPE html>
<html lang="en">
<head>
<meta charset="utf-8">
<title>plumbwick – IT Support</title>
<link rel="stylesheet" href="https://fonts.googleapis.com/css2?family=Oxygen:wght@400;700&family=Oswald:wght@400;500&display=swap">
<style>
:root{
  --plum:#8c1050;
  --plum-dark:#6d0c3f;
  --gold:#d4a900;
  --ink:#2d2d2d;
  --text:#3f3f3f;
  --grey-band:#ececec;
  --rule:#cfcfcf;
  --white:#ffffff;
}
*{margin:0;padding:0;box-sizing:border-box}
html,body{width:974px;height:1200px;overflow:hidden;background:var(--white)}
body{font-family:"Oxygen",Arial,sans-serif;color:var(--text)}
.page{position:relative;width:974px;height:1200px;overflow:hidden}
.abs{position:absolute}

/* header */
.topbar{left:0;top:0;width:974px;height:4px;background:var(--gold)}
.header{left:0;top:4px;width:974px;height:96px;background:linear-gradient(#ffffff,#f1f1f1);border-bottom:1px solid #ddd}
.brand{left:107px;top:22px;display:flex;align-items:center;gap:14px}
.brand-mark{width:40px;height:40px;background:var(--gold)}
.brand-name{font-size:38px;font-weight:700;color:var(--plum);letter-spacing:-0.5px;line-height:1}
.chat{left:730px;top:18px;width:130px;height:50px;border:1px solid #cfcfcf;border-radius:4px;background:#fafafa;display:flex;align-items:center}
.chat-photo{width:40px;height:48px;background:linear-gradient(#e7ddd5,#cbbfb6);border-radius:3px 0 0 3px}
.chat-text{font-family:"Oswald",sans-serif;font-size:15px;line-height:19px;margin-left:6px;text-transform:uppercase}
.chat-text .a{color:var(--plum)}
.chat-text .b{color:#2e7d1f}
.nav{left:296px;top:78px;display:flex;height:22px}
.nav a{display:block;font-size:11.5px;color:var(--plum);text-decoration:none;padding:5px 8.5px 0;text-transform:uppercase;letter-spacing:.2px}
.nav a.active{background:#333;color:var(--white);border-radius:2px 2px 0 0;padding:5px 6px 0}

/* hero */
.hero{left:0;top:100px;width:974px;height:362px;background:radial-gradient(ellipse at 60% 40%,#dbe8f2 0%,#9fb7cb 55%,#5f7890 100%)}
.hero-shade{left:0;top:100px;width:300px;height:362px;background:linear-gradient(90deg,rgba(20,24,30,.75),rgba(20,24,30,0))}
.caption{left:0;top:426px;width:974px;height:36px;background:rgba(40,42,48,.85)}
.caption-text{left:0;top:428px;width:974px;text-align:center;font-family:"Oswald",sans-serif;font-size:23px;color:var(--white)}
.dot{top:436px;width:15px;height:15px;border-radius:50%;background:var(--gold)}
.dot.on{background:var(--white)}
.hero-base{left:0;top:461px;width:974px;height:3px;background:#2b2b2b}

/* section titles */
.sec-head{left:0;width:974px;display:flex;justify-content:center;align-items:center;gap:8px;height:34px}
.sec-title{font-size:26px;font-weight:400;color:var(--ink);white-space:nowrap}
.sec-title span{color:var(--plum)}

/* about */
.about-text{left:124px;top:513px;width:726px;text-align:center;font-size:11.2px;line-height:17px;color:var(--text)}
.more{left:0;top:588px;width:974px;text-align:center;font-size:12.5px;font-weight:700;color:var(--plum)}

/* services */
.services{left:0;top:606px;width:974px;height:218px;background:var(--grey-band);border-top:1px solid #dcdcdc;border-bottom:1px solid #dcdcdc}
.svc{top:667px;width:150px;text-align:center}
.svc-ring{width:90px;height:90px;margin:0 auto;border:3px solid var(--gold);border-radius:50%;background:var(--white);display:flex;align-items:center;justify-content:center}
.svc-label{margin-top:20px;font-size:12px;font-weight:700;color:#333}

/* lower columns */
.col-title{top:852px;font-size:17px;color:var(--ink);display:flex;align-items:center;gap:6px}
.col-title span{color:var(--plum)}
.col-rule{top:879px;width:230px;height:1px;background:var(--rule)}
.news{left:115px;width:230px;font-size:10px;line-height:14px;color:#333}
.news b{display:block;font-size:11px;margin-bottom:5px}
.news-sep{left:115px;top:957px;width:226px;border-top:1px dashed #ccc}
.readmore{font-size:10.5px;font-weight:700;color:var(--plum)}
.quote{left:372px;top:896px;width:229px;height:104px;background:#ececec;border-radius:6px;padding:12px 10px 0 16px;font-size:11px;line-height:17px;font-style:italic;color:#444}
.qmark{font-family:Georgia,serif;font-size:30px;color:#c4c4c4;float:left;line-height:22px;margin-right:6px}
.avatar{left:388px;top:983px;width:54px;height:55px;border:2px solid #fff;box-shadow:0 0 2px #999;background:linear-gradient(#b9c2ca,#6c7a86)}
.client{left:455px;top:1014px;font-size:10px;font-weight:700;color:#333}
.field{left:632px;width:228px;border:1px solid #cfcfcf;border-radius:3px;background:#fff;font-size:10px;font-style:italic;color:#777;padding:5px 8px}
.submit{left:631px;top:1024px;width:55px;height:19px;background:var(--plum-dark);color:#fff;font-size:11.5px;font-weight:700;text-align:center;line-height:19px;border-radius:2px}

/* footer */
.footer{left:0;top:1075px;width:974px;height:125px;background:linear-gradient(#96144f,#6e0d3d);border-top:2px solid var(--gold)}
.fbox{top:1091px;height:62px;border:1px solid rgba(255,255,255,.25);background:rgba(255,255,255,.08);padding:6px 10px;color:#fff}
.fbox h4{font-family:Arial,sans-serif;font-size:12.5px;font-weight:700}
.subscribe-row{display:flex;gap:6px;margin-top:8px}
.email-in{width:146px;height:22px;background:#b5507f;border-radius:2px;font-size:10px;font-style:italic;color:#fff;padding:5px 8px}
.go{width:25px;height:22px;background:#3a0820;border-radius:2px;flex:none}
.fline{font-family:Arial,sans-serif;font-size:10px;margin-top:4px;display:flex;align-items:center;gap:8px}
.social{display:flex;gap:11px;margin-top:9px}
.social i{display:block;width:20px;height:20px;border-radius:3px;background:rgba(255,255,255,.55)}
.flogo{left:648px;top:1108px;display:flex;align-items:center;gap:16px}
.flogo-mark{width:40px;height:30px;background:#c98ca9}
.flogo-name{font-size:32px;font-weight:700;color:#e6cbd8}
.flinks{left:115px;top:1169px;font-family:Arial,sans-serif;font-size:10px;color:#fff;word-spacing:1px}
.copy{left:666px;top:1169px;font-family:Arial,sans-serif;font-size:10px;color:#fff}
</style>
</head>
<body>
<div class="page">
  <div class="abs topbar"></div>
  <header class="abs header"></header>
  <div class="abs brand"><div class="brand-mark"></div><div class="brand-name">plumbwick</div></div>
  <div class="abs chat">
    <div class="chat-photo" role="img" aria-label="Support agent wearing a headset"></div>
    <div class="chat-text"><div class="a">Live Chatt</div><div class="b">Available</div></div>
  </div>
  <nav class="abs nav">
    <a class="active">Home</a><a>About Us</a><a>What We Do</a><a>News Blog</a><a>Articles</a><a>Clients</a><a>Partners</a><a>Contact Us</a>
  </nav>

  <div class="abs hero" role="img" aria-label="Businessman touching a glowing world map network of connected nodes"></div>
  <div class="abs hero-shade"></div>
  <div class="abs caption"></div>
  <div class="abs caption-text">Serious IT Support For Business</div>
  <div class="abs dot on" style="left:771px"></div>
  <div class="abs dot" style="left:794px"></div>
  <div class="abs dot" style="left:817px"></div>
  <div class="abs dot" style="left:840px"></div>
  <div class="abs hero-base"></div>

  <div class="abs sec-head" style="top:472px">
    <svg width="215" height="16"><g stroke="#333" stroke-width="1.3"><path d="M0 7 L215 5 M45 10 L215 9 M110 13 L210 12"/></g></svg>
    <h2 class="sec-title">About <span>plumbwick</span></h2>
    <svg width="215" height="16"><g stroke="#333" stroke-width="1.3"><path d="M0 5 L215 7 M0 9 L170 10 M5 12 L105 13"/></g></svg>
  </div>
  <p class="abs about-text">Plumbwick was established with a specific aim: to consistently deliver an advanced and comprehensive IT service for ambitious growing companies across many industry sectors. We aim to provide the very best in service and support, and to aid business growth through the effective and skilled use of modern IT solutions. Founded in 2003, we have grown rapidly and have delivered successful business solutions to small and medium sized businesses, working with customers across a wide IT spectrum. The knowledge...</p>
  <div class="abs more">More +</div>

  <section class="abs services"></section>
  <div class="abs sec-head" style="top:621px">
    <svg width="210" height="16"><g stroke="#333" stroke-width="1.3"><path d="M0 5 L210 7 M45 9 L210 10 M110 13 L205 13"/></g></svg>
    <h2 class="sec-title">Our <span>Services</span></h2>
    <svg width="210" height="16"><g stroke="#333" stroke-width="1.3"><path d="M0 7 L210 5 M0 10 L165 9 M5 13 L100 13"/></g></svg>
  </div>

  <div class="abs svc" style="left:115px"><div class="svc-ring">
    <svg width="46" height="60" viewBox="0 0 46 60"><path d="M14 6 C6 8 6 22 16 32 C22 38 30 38 33 32 L28 26 L24 29 C19 26 16 21 15 16 L19 13 Z" fill="#8c1050"/><path d="M22 38 C22 46 14 46 14 52" stroke="#8c1050" stroke-width="2" fill="none"/><ellipse cx="22" cy="54" rx="10" ry="5" fill="#8c1050"/></svg>
  </div><div class="svc-label">It Support &amp; Management</div></div>

  <div class="abs svc" style="left:268px"><div class="svc-ring">
    <svg width="58" height="44" viewBox="0 0 58 44"><path d="M14 34 A10 10 0 0 1 12 14 A13 13 0 0 1 36 8 A11 11 0 0 1 48 34 Z" fill="#8c1050"/><path d="M22 40 L36 22 M30 22 L36 22 L36 28 M20 34 L20 40 L26 40" stroke="#fff" stroke-width="3" fill="none"/></svg>
  </div><div class="svc-label">Cloud Computing</div></div>

  <div class="abs svc" style="left:422px"><div class="svc-ring">
    <svg width="50" height="52" viewBox="0 0 50 52"><rect x="2" y="2" width="46" height="48" rx="6" fill="#8c1050"/><rect x="9" y="13" width="32" height="22" rx="2" fill="#fff"/><rect x="13" y="17" width="24" height="14" fill="#8c1050"/><rect x="12" y="40" width="26" height="4" fill="#fff"/></svg>
  </div><div class="svc-label">Disaster Recovery</div></div>

  <div class="abs svc" style="left:567px"><div class="svc-ring">
    <svg width="50" height="54" viewBox="0 0 50 54"><path d="M25 2 L48 12 L48 34 L25 52 L2 34 L2 12 Z" fill="#8c1050"/><path d="M2 12 L25 22 L48 12 M25 22 L25 52" stroke="#fff" stroke-width="2.5" fill="none"/></svg>
  </div><div class="svc-label">Virtualisation</div></div>

  <div class="abs svc" style="left:715px"><div class="svc-ring">
    <svg width="46" height="56" viewBox="0 0 46 56"><circle cx="23" cy="8" r="5" fill="#8c1050"/><path d="M21 12 L6 54 M25 12 L40 54 M6 34 L40 34" stroke="#8c1050" stroke-width="3.5" fill="none"/></svg>
  </div><div class="svc-label">CAD Services</div></div>

  <div class="abs col-title" style="left:115px"><svg width="20" height="16"><path d="M2 5 H6 L15 1 V15 L6 11 H2 Z" fill="#444"/></svg>Latest <span>News</span></div>
  <div class="abs col-rule" style="left:115px"></div>
  <div class="abs news" style="top:894px"><b>04/17/2014</b>Lorem ipsum dolor sit amet, cctetuer adipiscingin elit, sed diam nummy nibh eui smod tinciduntiotvulputate velit esse olestie</div>
  <div class="abs news-sep"></div>
  <div class="abs news" style="top:965px"><b>04/17/2014</b>Lorem ipsum dolor sit amet, cctetuer adipiscingin elit, sed diam nummy nibh eui smod tinciduntiotvulputate velit esse olestie</div>
  <div class="abs readmore" style="left:286px;top:1034px">Read more »</div>

  <div class="abs col-title" style="left:372px"><svg width="20" height="18"><path d="M1 2 H13 V10 H6 L3 13 V10 H1 Z" fill="#444"/><path d="M8 12 H16 L19 15 V6 H15 V12" fill="#444"/></svg>Client <span>Testimonials</span></div>
  <div class="abs col-rule" style="left:372px"></div>
  <div class="abs quote"><span class="qmark">“</span>Duis autem vel eum iriureol hder in vultat velit esse moles conqat vela ilu dolor feugiat.Duis autem vel eum ure hendrern vultat velit esse autm vel eum</div>
  <svg class="abs" style="left:560px;top:999px" width="30" height="14"><path d="M0 0 H30 L4 14 Z" fill="#ececec"/></svg>
  <div class="abs avatar" role="img" aria-label="Client portrait photo"></div>
  <div class="abs client">Mr. Lorem Ipsum Dolor</div>
  <div class="abs readmore" style="left:545px;top:1035px">Read more »</div>

  <div class="abs col-title" style="left:631px"><svg width="20" height="18"><path d="M2 2 H11 V5 M2 2 V16 H13 V12" stroke="#444" stroke-width="2" fill="none"/><path d="M8 12 L17 3 L19 5 L10 14 L7 15 Z" fill="#444"/></svg>Quick <span>Contact</span></div>
  <div class="abs col-rule" style="left:631px"></div>
  <div class="abs field" style="top:896px;height:22px">Name</div>
  <div class="abs field" style="top:925px;height:22px">Email</div>
  <div class="abs field" style="top:953px;height:58px">Message</div>
  <div class="abs submit">Submit</div>

  <footer class="abs footer"></footer>
  <div class="abs fbox" style="left:115px;width:200px"><h4>Subscribe to Newsletter</h4>
    <div class="subscribe-row"><span class="email-in">Email here</span><span class="go"><svg width="25" height="22"><path d="M10 6 L15 11 L10 16" stroke="#fff" stroke-width="2.5" fill="none"/></svg></span></div>
  </div>
  <div class="abs fbox" style="left:337px;width:130px"><h4>Contact Us</h4>
    <div class="fline" style="margin-top:6px"><svg width="10" height="10"><path d="M2 1 L4 1 L5 4 L3.5 5 C4 6.5 5 7 6 7.5 L7 6 L10 7 V9 C5 10 0 5 1 1 Z" fill="#d88fb0"/></svg>020-555-0148</div>
    <div class="fline"><svg width="10" height="8"><rect x="0.5" y="0.5" width="9" height="7" fill="none" stroke="#d88fb0"/><path d="M0.5 0.5 L5 4.5 L9.5 0.5" stroke="#d88fb0" fill="none"/></svg>info@plumbwick.com</div>
  </div>
  <div class="abs fbox" style="left:490px;width:96px"><h4>Follow Us</h4><div class="social"><i></i><i></i><i></i></div></div>
  <div class="abs flogo"><div class="flogo-mark"></div><div class="flogo-name">plumbwick</div></div>
  <div class="abs flinks">Home &nbsp;|&nbsp; About Us &nbsp;|&nbsp; What we do &nbsp;|&nbsp; News Blog &nbsp;|&nbsp; Articles &nbsp;|&nbsp; Clients &nbsp;|&nbsp; Partners &nbsp;|&nbsp; Terms &nbsp;|&nbsp; Support &nbsp;|&nbsp; Contact</div>
  <div class="abs copy">© 2014 plumbwick. All Rights Reserved.</div>
</div>
</body>
</html>
```